Working Capital graphics

Our business advisory firm requires 9 images to be re-created and improved in the branding of our business.

The 9 images have been uploaded below and the colours and branding of the business can be found at the website www.tallowmereadvisory.com.au

```html
<!DOCTYPE html>
<html lang="en">
<head>
<meta charset="utf-8">
<title>Payables Drivers</title>
<link rel="stylesheet" href="https://fonts.googleapis.com/css2?family=Montserrat:ital,wght@0,700;1,700;1,800&display=swap">
<style>
  :root {
    --canvas: #ffffff;
    --brand-navy: #1d3557;
    --brand-navy-deep: #152844;
    --brand-gold: #e8a93a;
    --brand-sky: #a9c7e8;
    --white: #ffffff;
    --ink: #1d3557;
  }
  * { box-sizing: border-box; margin: 0; padding: 0; }
  html, body { width: 1200px; height: 1000px; overflow: hidden; background: var(--canvas); }
  body { position: relative; font-family: "Montserrat", Arial, sans-serif; }

  .panel {
    position: absolute; left: 26px; top: 138px; width: 1154px; height: 732px;
    background: linear-gradient(160deg, var(--brand-navy) 0%, var(--brand-navy-deep) 100%);
    border-radius: 6px;
  }
  .panel-title {
    position: absolute; left: 45px; top: 168px;
    color: var(--white); font-size: 52px; font-weight: 800; font-style: italic; letter-spacing: 0;
  }
  .column-heading {
    position: absolute; left: 600px; top: 162px; width: 290px; text-align: center;
    color: var(--brand-gold); font-size: 34px; font-weight: 700;
  }
  .source-box {
    position: absolute; left: 38px; top: 418px; width: 236px; height: 232px;
    background: var(--white); border-radius: 6px; border-left: 8px solid var(--brand-gold);
    display: flex; align-items: center; justify-content: center;
    text-align: center; color: var(--ink); font-size: 29px; font-weight: 700; font-style: italic; line-height: 1.3;
  }
  .connectors { position: absolute; left: 0; top: 0; }
  .driver-bar {
    position: absolute; left: 418px; width: 678px; height: 64px;
    background: var(--white); border-radius: 0 6px 6px 0;
    display: flex; align-items: center; justify-content: center;
    padding-left: 20px; color: var(--ink); font-size: 26px; font-weight: 700; font-style: italic;
  }
  .driver-number {
    position: absolute; left: 378px; width: 80px; height: 80px; border-radius: 50%;
    background: var(--brand-gold); border: 3px solid var(--white);
    display: flex; align-items: center; justify-content: center;
    color: var(--brand-navy); font-size: 38px; font-weight: 800; font-style: italic; letter-spacing: -2px;
  }
</style>
</head>
<body>
  <div class="panel"></div>
  <div class="panel-title">Payables</div>
  <div class="column-heading">Drivers</div>

  <svg class="connectors" width="1200" height="1000" aria-hidden="true">
    <g stroke="#a9c7e8" stroke-width="2" fill="none">
      <line x1="274" y1="535" x2="390" y2="535"/>
      <line x1="351" y1="292" x2="351" y2="776"/>
      <line x1="351" y1="292" x2="390" y2="292"/>
      <line x1="351" y1="411" x2="390" y2="411"/>
      <line x1="351" y1="654" x2="390" y2="654"/>
      <line x1="351" y1="776" x2="390" y2="776"/>
    </g>
  </svg>

  <div class="source-box">Payables<br>Drivers</div>

  <div class="driver-bar" style="top:258px">Reduce early payments</div>
  <div class="driver-number" style="top:250px">14</div>

  <div class="driver-bar" style="top:384px">Reduce over-rides</div>
  <div class="driver-number" style="top:376px">15</div>

  <div class="driver-bar" style="top:503px">Reduce vendor credits</div>
  <div class="driver-number" style="top:495px">16</div>

  <div class="driver-bar" style="top:622px">Increase PO vendor terms</div>
  <div class="driver-number" style="top:614px">17</div>

  <div class="driver-bar" style="top:744px">Increase invoice only terms</div>
  <div class="driver-number" style="top:736px">18</div>
</body>
</html>
```